Falkrin homes and renovations business card design.

Would like some new card designs utilizing my new logo that look professional. I am open to different colors on the logo or utilize the same ones we have. I like the original concept but would like to see some fresh ideas and build on what we have already done.

Target Market(s)

Custom home building industry, Real estate sales, Renovation projects.

Industry/Entity Type

Home Builder

Contact Information for Business Card

Falkrin Homes and Renovations
2871 96th Avenue
Frank, Alberta
T2R3W8
Home : 403- 718-4063 Cell: 403- 294-5170

My info is : Dax Falkrin, President and CEO
email: falkrinhomes@maildrop-example.net
Website: falkrinhomes-example.com
websit

Requirements
Must have
• Must Use my new logo design. I am open to different colors on the logo or utilize the same ones in the existing design. I can upload the original logo design if needed.

```html
<!DOCTYPE html>
<html lang="en">
<head>
<meta charset="utf-8">
<title>Falkrin Homes and Renovations – Business Card</title>
<link href="https://fonts.googleapis.com/css2?family=Montserrat:wght@400;500;600&display=swap" rel="stylesheet">
<style>
  :root {
    --backdrop: #d6d7d9;
    --card-light: #ffffff;
    --card-dark: #414143;
    --accent-yellow: #f2b81c;
    --accent-gold: #b78a2e;
    --fold-shade: #c9961a;
    --ink: #444446;
  }
  * { margin: 0; padding: 0; box-sizing: border-box; }
  html, body {
    width: 1200px; height: 800px; overflow: hidden;
    background: var(--backdrop);
    font-family: "Montserrat", sans-serif;
  }
  .card {
    position: absolute; left: 346px; width: 510px; height: 282px;
    border-radius: 16px; overflow: hidden;
  }
  .card--front { top: 70px; background: var(--card-light); }
  .card--back { top: 410px; background: var(--card-dark); }

  .brand {
    position: absolute; left: 0; width: 100%;
    display: flex; align-items: center; justify-content: center; gap: 8px;
    color: var(--accent-gold); font-weight: 600; white-space: nowrap;
  }
  .brand__mark { background: var(--accent-gold); }
  .card--front .brand { top: 34px; font-size: 13px; }
  .card--front .brand__mark { width: 9px; height: 9px; }
  .card--back .brand { top: 124px; font-size: 24px; }
  .card--back .brand__mark { width: 16px; height: 16px; }

  .rule {
    position: absolute; left: 0; width: 100%; height: 3px;
    background: var(--accent-yellow);
  }
  .rule--top { top: 104px; }
  .rule--bottom { top: 249px; }

  .banner { position: absolute; left: 139px; top: 79px; width: 231px; height: 53px; }
  .holder { position: absolute; left: 0; width: 100%; text-align: center; }
  .holder__name { top: 87px; color: #fff; font-size: 24px; font-weight: 500; letter-spacing: 0.3px; }
  .holder__title { top: 111px; color: #fff; font-size: 13px; font-weight: 400; }

  .icons { position: absolute; top: 142px; left: 204px; display: flex; gap: 15px; }
  .icons svg { width: 24px; height: 24px; display: block; }

  .contact {
    position: absolute; left: 0; width: 100%; text-align: center;
    color: var(--ink); font-size: 15px; font-weight: 400; line-height: 18px;
  }
  .contact--phones { top: 168px; }
  .contact--web { top: 207px; }
  .address { top: 257px; }
</style>
</head>
<body>
  <section class="card card--front">
    <div class="brand"><span class="brand__mark"></span>Falkrin Homes and Renovations</div>
    <div class="rule rule--top"></div>
    <svg class="banner" viewBox="0 0 231 53" aria-hidden="true">
      <polygon points="0,0 8,0 8,26 0,26" fill="var(--fold-shade)"/>
      <polygon points="223,0 231,0 231,26 223,26" fill="var(--fold-shade)"/>
      <polygon points="8,0 223,0 216,53 16,53" fill="var(--accent-yellow)"/>
    </svg>
    <div class="holder holder__name">Dax Falkrin</div>
    <div class="holder holder__title">President and CEO</div>

    <div class="icons">
      <svg viewBox="0 0 24 24" aria-label="Phone"><circle cx="12" cy="12" r="12" fill="var(--accent-yellow)"/><rect x="8.5" y="5.5" width="7" height="13" rx="1.2" fill="none" stroke="#fff" stroke-width="1.3"/><line x1="11" y1="16.3" x2="13" y2="16.3" stroke="#fff" stroke-width="1"/></svg>
      <svg viewBox="0 0 24 24" aria-label="Email"><circle cx="12" cy="12" r="12" fill="var(--accent-yellow)"/><rect x="6" y="8" width="12" height="8.5" fill="none" stroke="#fff" stroke-width="1.3"/><polyline points="6,8 12,13 18,8" fill="none" stroke="#fff" stroke-width="1.2"/></svg>
      <svg viewBox="0 0 24 24" aria-label="Website"><circle cx="12" cy="12" r="12" fill="var(--accent-yellow)"/><circle cx="12" cy="12" r="6.5" fill="none" stroke="#fff" stroke-width="1.2"/><ellipse cx="12" cy="12" rx="3" ry="6.5" fill="none" stroke="#fff" stroke-width="1"/><line x1="5.5" y1="12" x2="18.5" y2="12" stroke="#fff" stroke-width="1"/></svg>
    </div>

    <div class="contact contact--phones">403- 718-4063<br>403- 294-5170</div>
    <div class="contact contact--web">falkrinhomes@maildrop-example.net<br>www.falkrinhomes-example.com</div>
    <div class="rule rule--bottom"></div>
    <div class="contact address">2871 96th Avenue Frank, Alberta</div>
  </section>

  <section class="card card--back">
    <div class="brand"><span class="brand__mark"></span>Falkrin Homes and Renovations</div>
  </section>
</body>
</html>
```